Red Mo's Wine Label Project

We need a new entry level wine label called "Red Mo's" for a range of wines we are developing from inland Australia. Our company is made up of three youngish guys who live hard and love taking the mickey. Red Mo is Red Morrie - the largest and loudest of the three partners (and ideally this label will take the mickey out of him). We've grown the grapes ourselves for this first release which will be a 2012 Pinot Gris. Wine style is dry, young, fresh and contemporary and pitched at the sub AUD $10 retail price point. The package will be flint (clear) claret shape bottle with plain screwcap (colour matched to suit the winning label design).

I've attached a couple of photos of Red Morrie to give you some idea of his presence and persona.

Target Market(s)

Semi educated 25 - 40 year old wine drinkers. Skewed towards females.

Industry/Entity Type

Retail

Requirements
Should not have
• Anything traditional or old fashioned

```html
<!DOCTYPE html>
<html lang="en">
<head>
<meta charset="utf-8">
<title>Red Mo's Pinot Gris 2012 – Label Set</title>
<link rel="stylesheet" href="https://fonts.googleapis.com/css2?family=Oswald:wght@600&family=Questrial&display=swap">
<style>
  :root {
    --canvas-bg: #f4f4f4;
    --label-paper: #ffffff;
    --ink: #1f1d1d;
    --band-text: #ffffff;
    --green-top: #7db56c;
    --green-bottom: #a3d394;
    --rose-top: #c92f66;
    --rose-bottom: #d4457a;
    --engraving-light: #e2e2e2;
    --engraving-mid: #a8a8a8;
    --engraving-dark: #6a6a6a;
  }
  * { box-sizing: border-box; margin: 0; padding: 0; }
  html, body {
    width: 1037px;
    height: 1200px;
    overflow: hidden;
    background: var(--canvas-bg);
  }
  .label-set {
    position: relative;
    width: 1037px;
    height: 1200px;
  }
  .label {
    position: absolute;
    top: 140px;
    width: 300px;
    height: 920px;
    background: var(--label-paper);
    box-shadow: 0 2px 10px rgba(0,0,0,0.12);
    display: flex;
    flex-direction: column;
  }
  .label--white { left: 140px; }
  .label--rose { left: 597px; }

  .label__brand {
    height: 190px;
    display: flex;
    align-items: center;
    justify-content: center;
    font-family: "Oswald", sans-serif;
    font-weight: 600;
    font-size: 66px;
    letter-spacing: 1px;
    color: var(--ink);
    line-height: 1;
    padding: 20px 30px 0;
    white-space: nowrap;
  }
  .label__artwork {
    flex: 1;
    margin: 10px 40px 30px;
    border-radius: 4px;
  }
  .label--white .label__artwork {
    background: radial-gradient(ellipse at 50% 45%, var(--engraving-light), var(--engraving-dark));
  }
  .label--rose .label__artwork {
    margin: 10px 60px 30px;
    background: radial-gradient(ellipse at 50% 40%, var(--engraving-light), var(--engraving-mid) 60%, var(--engraving-dark));
  }
  .label__band {
    height: 250px;
    color: var(--band-text);
    font-family: "Questrial", sans-serif;
    text-align: center;
    display: flex;
    flex-direction: column;
    justify-content: center;
    align-items: center;
    padding-top: 10px;
  }
  .label--white .label__band { background: linear-gradient(180deg, var(--green-top), var(--green-bottom)); }
  .label--rose .label__band { background: linear-gradient(180deg, var(--rose-top), var(--rose-bottom)); }
  .label__variety { font-size: 30px; letter-spacing: 1px; line-height: 1.2; }
  .label__alcohol { font-size: 26px; letter-spacing: 1px; line-height: 1.2; }
  .label__vintage { font-size: 76px; letter-spacing: 2px; line-height: 1.1; margin-top: 4px; }
</style>
</head>
<body>
  <main class="label-set">
    <section class="label label--white">
      <h1 class="label__brand">RED MO</h1>
      <div class="label__artwork" role="img" aria-label="Engraved illustration of a vintage wine press"></div>
      <div class="label__band">
        <p class="label__variety">PINOT GRIS</p>
        <p class="label__alcohol">ALKOHOL 12%</p>
        <p class="label__vintage">2012</p>
      </div>
    </section>

    <section class="label label--rose">
      <h1 class="label__brand">RED MO</h1>
      <div class="label__artwork" role="img" aria-label="Engraved illustration of a T-handle corkscrew"></div>
      <div class="label__band">
        <p class="label__variety">PINOT GRIS</p>
        <p class="label__alcohol">ALKOHOL 12%</p>
        <p class="label__vintage">2012</p>
      </div>
    </section>
  </main>
</body>
</html>
```